So the ones in the picture are my original cards that I came up with. 😅however I kinda messed up on two things, I missed spelled my name it should be Marcello Vandora as well as the email should be Marcellov@brightlanecrews.com. I would like to clean this card up and also make it pop! Something that people would remember me by and that screams DEMOLITION. As well as a card that give you a feeling of loyalty and trust. I would also like to change and remove junk hauling and add full demolition to replace it. These cards worked for a little while but I cant make that my image while handing these out. I would also like to only put down that we are located in Maple Crest Vista, CA, 92000 instead of the address on the card. Also if we can have a line that states Licensed, Bonded, & Insured. With out License # 4837215

Target Market(s)

Contractors and Home owners

Industry/Entity Type

Construction specialist in Demolition

Contact Information for Business Card

R Wrecking Selective Demolition & Full Demolition Kitchens AD Preparation Bathrooms Sheds Interiors & Exteriors Demo Digging And Much More Marcello Vandora Owner our city state and zip

Font styles to use
Serif
Sans Serif
Decorative

Colors
0054AA
0677BA
7BADD7
CADEEF
E8F1F8
0094D4
00A9DD
6FCCEA
C7EBF8
E9F6FB

Requirements
Must have
• License# 4837215
Nice to have
• Trying to go with a blue and white color scheme
Should not have
• Building construction

```html
<!DOCTYPE html>
<html lang="en">
<head>
<meta charset="utf-8">
<title>RK Wrecking – Business Cards</title>
<link href="https://fonts.googleapis.com/css2?family=Open+Sans:wght@400;600;700&family=Oswald:wght@500;600&display=swap" rel="stylesheet">
<style>
  :root{
    --stage:#232323;
    --card-blue:#0c4f9c;
    --card-blue-deep:#1a3f80;
    --card-dark:#1e1e21;
    --band-1:#2a2a2e;
    --band-2:#242428;
    --accent:#0054aa;
    --accent-bright:#1f6fd1;
    --white:#ffffff;
    --text-soft:#e9f1f8;
  }
  *{margin:0;padding:0;box-sizing:border-box}
  html,body{width:1200px;height:780px;overflow:hidden;background:var(--stage)}
  .stage{position:relative;width:1200px;height:780px}
  .card{
    position:absolute;top:90px;width:340px;height:600px;border-radius:28px;overflow:hidden;
    box-shadow:0 18px 40px rgba(0,0,0,.55);
  }
  /* back side */
  .card--back{left:190px;background:var(--card-blue)}
  .back-mark{
    position:absolute;left:50%;top:50%;transform:translate(-50%,-50%) rotate(90deg);
    display:flex;flex-direction:column;align-items:flex-start;white-space:nowrap;
  }
  .back-mark__name{
    font-family:"Open Sans",sans-serif;font-weight:700;font-size:62px;line-height:1;
    color:var(--card-blue-deep);letter-spacing:1px;
  }
  .back-mark__license{
    font-family:"Open Sans",sans-serif;font-weight:600;font-size:18px;color:var(--card-blue-deep);
    margin-top:6px;letter-spacing:1px;
  }
  /* front side */
  .card--front{left:670px;background:var(--card-dark);color:var(--white);font-family:"Open Sans",sans-serif;text-align:center}
  .card__bands{position:absolute;inset:0}
  .card__content{position:relative;height:100%;display:flex;flex-direction:column;align-items:center;padding-top:40px}
  .brand{display:flex;align-items:center;gap:10px}
  .brand__dot{width:16px;height:16px;border-radius:50%;background:var(--accent-bright)}
  .brand__name{font-weight:700;font-size:30px;color:var(--white);letter-spacing:.5px}
  .brand__license{font-size:10px;font-weight:600;letter-spacing:1px;color:var(--white);margin-top:2px}
  .person__name{margin-top:34px;font-weight:700;font-size:30px;color:var(--accent-bright);line-height:1.1}
  .person__role{font-size:14px;font-weight:600;margin-top:2px}
  .icon-row{display:flex;gap:10px;margin:12px 0 8px}
  .icon{width:24px;height:24px}
  .contact{font-size:14px;line-height:1.45}
  .contact__pin{margin:12px 0 6px}
  .services{margin-top:auto;margin-bottom:48px}
  .services__title{font-weight:700;font-size:30px;color:var(--accent-bright);line-height:1.1}
  .services__tag{font-family:"Oswald",sans-serif;font-weight:500;font-size:12px;letter-spacing:.2px;margin:2px 0 8px}
  .services__list{list-style:none;font-size:15px;line-height:1.45}
</style>
</head>
<body>
<div class="stage">

  <section class="card card--back" aria-label="Card back">
    <div class="back-mark">
      <span class="back-mark__name">RK Wrecking</span>
      <span class="back-mark__license">LICENSE#4837215</span>
    </div>
  </section>

  <section class="card card--front" aria-label="Card front">
    <svg class="card__bands" viewBox="0 0 340 600" preserveAspectRatio="none" aria-hidden="true">
      <path d="M0 0H340V250C300 330 180 360 0 350Z" fill="var(--band-1)"/>
      <path d="M0 350C180 360 300 330 340 250V330C250 380 150 400 70 430L0 440Z" fill="var(--band-2)"/>
    </svg>
    <div class="card__content">
      <div class="brand">
        <span class="brand__dot"></span>
        <span class="brand__name">RK Wrecking</span>
      </div>
      <div class="brand__license">LICENSE#4837215</div>

      <h1 class="person__name">Marcello Vandora</h1>
      <p class="person__role">Owner our city state and zip</p>

      <div class="icon-row">
        <svg class="icon" viewBox="0 0 24 24" aria-label="Phone"><circle cx="12" cy="12" r="12" fill="var(--accent-bright)"/><path d="M8 7c1 0 1.5 2 1.5 2.5S8.5 11 8.5 11c.8 1.8 2.5 3.5 4.5 4.5 0 0 1-1 1.5-1s2.5.5 2.5 1.5-1 2-2 2C10 18 6 14 6 9c0-1 1-2 2-2z" fill="#fff"/></svg>
        <svg class="icon" viewBox="0 0 24 24" aria-label="Email"><circle cx="12" cy="12" r="12" fill="var(--accent-bright)"/><rect x="6" y="8" width="12" height="9" rx="1" fill="none" stroke="#fff" stroke-width="1.5"/><path d="M6.5 8.5 12 13l5.5-4.5" fill="none" stroke="#fff" stroke-width="1.5"/></svg>
        <svg class="icon" viewBox="0 0 24 24" aria-label="Website"><circle cx="12" cy="12" r="12" fill="var(--accent-bright)"/><circle cx="12" cy="12" r="6" fill="none" stroke="#fff" stroke-width="1.4"/><path d="M6 12h12M12 6c-2.5 3-2.5 9 0 12M12 6c2.5 3 2.5 9 0 12" fill="none" stroke="#fff" stroke-width="1.2"/></svg>
      </div>

      <p class="contact">(555) 218-4630<br>info@brightlanecrews.com<br>Marcellov@brightlanecrews.com</p>

      <svg class="icon contact__pin" viewBox="0 0 24 24" aria-label="Location"><circle cx="12" cy="12" r="12" fill="var(--accent-bright)"/><path d="M12 5a4 4 0 0 1 4 4c0 3-4 8-4 8s-4-5-4-8a4 4 0 0 1 4-4z" fill="#fff"/><circle cx="12" cy="9" r="1.5" fill="var(--accent-bright)"/></svg>
      <p class="contact">Maple Crest Vista,<br>CA, 92000</p>

      <div class="services">
        <h2 class="services__title">R Wrecking</h2>
        <p class="services__tag">R WRECKING SELECTIVE DEMOLITION &amp; FULL DEMOLITION</p>
        <ul class="services__list">
          <li>Sheds</li>
          <li>Digging</li>
          <li>Kitchens</li>
          <li>Bathrooms</li>
          <li>AD Preparation</li>
          <li>Interiors &amp; Exteriors Demo</li>
        </ul>
      </div>
    </div>
  </section>

</div>
</body>
</html>
```